business card

Business card for new business.
Red and black corporate colors.
Card can have an Indsutrial feel to it. Feel free to add Rust, Bolted steel, or graphics as you see fit. We provide highly specialized services to the below mentioned industries.
Keep information out of corners so that if I want I can choose rounded corners.
Information
- front. name - title - phone - email
- Rear
Refining - Rail - Infrastructure - Mining - Energy
Calgary - Edmonton - Fort McMurray - Revelstoke - Vancouver

```html
<!DOCTYPE html>
<html lang="en">
<head>
<meta charset="utf-8">
<title>Ironvale Business Card</title>
<link rel="stylesheet" href="https://fonts.googleapis.com/css2?family=Roboto:wght@400;500&family=Roboto+Condensed:wght@700&display=swap">
<style>
  :root {
    --backdrop: #2b2b2b;
    --steel-light: #f4f4f4;
    --steel-mid: #dcdcdc;
    --steel-dark: #c9c9c9;
    --brand-red: #e2001a;
    --rule-grey: #8a8a8a;
    --graphite: #7a7a7a;
    --ink: #5a5a5a;
    --white: #ffffff;
  }
  * { margin: 0; padding: 0; box-sizing: border-box; }
  html, body {
    width: 1200px; height: 960px; overflow: hidden;
    background: var(--backdrop);
    font-family: "Roboto", Arial, sans-serif;
  }
  .canvas { position: relative; width: 1200px; height: 960px; }
  .card {
    position: absolute; width: 600px; height: 342px; overflow: hidden;
    background: linear-gradient(90deg, var(--steel-mid) 0%, var(--steel-light) 30%, var(--steel-light) 60%, var(--steel-dark) 100%);
  }
  .card--front { left: 314px; top: 113px; }
  .card--back { left: 311px; top: 472px; }

  .wordmark {
    position: absolute; top: 80px; left: 0; width: 100%;
    display: flex; justify-content: center; align-items: center; gap: 14px;
  }
  .wordmark__square { width: 22px; height: 22px; background: var(--brand-red); }
  .wordmark__name {
    font-family: "Roboto Condensed", "Arial Narrow", sans-serif;
    font-weight: 700; font-size: 60px; letter-spacing: 1px;
    color: var(--graphite); line-height: 1;
  }

  .band { position: absolute; left: 0; top: 216px; width: 600px; height: 126px; }

  .contact {
    position: absolute; left: 30px; top: 257px;
    list-style: none; color: var(--white); font-size: 14px; line-height: 19px;
  }
  .contact li { display: flex; align-items: center; gap: 8px; }
  .contact svg { width: 13px; height: 13px; flex: none; }

  .person {
    position: absolute; right: 30px; top: 262px; text-align: right; color: var(--white);
  }
  .person__name {
    font-family: "Roboto Condensed", "Arial Narrow", sans-serif;
    font-weight: 700; font-size: 22px; line-height: 26px;
  }
  .person__title { font-size: 14px; font-weight: 500; line-height: 18px; }

  .back-mark {
    position: absolute; top: 118px; left: 0; width: 100%;
    display: flex; justify-content: center; align-items: center; gap: 12px;
  }
  .back-mark__square { width: 18px; height: 18px; background: var(--brand-red); }
  .back-mark__name {
    font-family: "Roboto Condensed", "Arial Narrow", sans-serif;
    font-weight: 700; font-size: 44px; color: var(--graphite); line-height: 1;
  }

  .sectors {
    position: absolute; top: 257px; left: 0; width: 100%;
    text-align: center; color: var(--ink); font-size: 14.5px; line-height: 18px;
  }
  .sectors .dot { color: var(--brand-red); padding: 0 3px; }
</style>
</head>
<body>
<main class="canvas">
  <section class="card card--front">
    <div class="wordmark">
      <span class="wordmark__square"></span>
      <span class="wordmark__name">IRONVALE</span>
    </div>

    <svg class="band" viewBox="0 0 600 126" aria-hidden="true">
      <polygon points="0,0 488,0 511,20 534,0 600,0 600,6 537,6 511,28 485,6 0,6" fill="var(--rule-grey)"/>
      <polygon points="0,7 485,7 511,29 537,7 600,7 600,126 0,126" fill="var(--brand-red)"/>
    </svg>

    <ul class="contact">
      <li>
        <svg viewBox="0 0 24 24"><path fill="#fff" d="M6.6 10.8a15.1 15.1 0 0 0 6.6 6.6l2.2-2.2c.3-.3.7-.4 1-.2 1.1.4 2.3.6 3.6.6.6 0 1 .4 1 1V20c0 .6-.4 1-1 1A17 17 0 0 1 3 4c0-.6.4-1 1-1h3.5c.6 0 1 .4 1 1 0 1.3.2 2.5.6 3.6.1.3 0 .7-.2 1z"/></svg>
        604 555 0187
      </li>
      <li>
        <svg viewBox="0 0 24 24"><path fill="#fff" d="M2 5h20v14H2z"/><path fill="none" stroke="var(--brand-red)" stroke-width="2" d="M2 5l10 8 10-8"/></svg>
        info@ironvale.com
      </li>
      <li>
        <svg viewBox="0 0 24 24"><circle cx="12" cy="12" r="10" fill="#fff"/><path fill="none" stroke="var(--brand-red)" stroke-width="1.6" d="M2 12h20M12 2c3 3 3 17 0 20M12 2c-3 3-3 17 0 20"/></svg>
        www.ironvale.com
      </li>
    </ul>

    <div class="person">
      <p class="person__name">MARK ELLISON</p>
      <p class="person__title">CEO/FOUNDER</p>
    </div>
  </section>

  <section class="card card--back">
    <div class="back-mark">
      <span class="back-mark__square"></span>
      <span class="back-mark__name">IRONVALE</span>
    </div>
    <div class="sectors">
      <p>Pipelines<span class="dot">•</span>Marine<span class="dot">•</span>Construction<span class="dot">•</span>Forestry</p>
      <p>Power<span class="dot">•</span>Ashford<span class="dot">•</span>Millbrook<span class="dot">•</span>Port Haldane</p>
      <p>Stonebridge<span class="dot">•</span>Westmere</p>
    </div>
  </section>
</main>
</body>
</html>
```